ULMIRA card Technical Architecture

Hello everyone ULMIRA: It is a consulting firm in Architecture and Construction. I require a card duplexing, sober, elegant, classic but not boring. Update 1: Use the following data for the card. Name: Gonzalo Pereda Mauricio Villalta Position: COO Twitter: @ulmiraAT Homepage: ulmira-example.com home address not include the participation of all thank you.

Target Market(s)

Construction companies, Architects and Consulting Engineers

Industry/Entity Type

Consulting

Contact Information for Business Card

Los campos que debe tener:
Nombre, Cargo, email, homepage y twitter

Font styles to use
Serif
Sans Serif
Other font styles liked:
• Me gustan playfair display, open sans y roboto, pero estoy sujeto a sus propuestas

Requirements
Must have
• Colors: Present combined proposals in white, red, gray and black Update 1: The two names must be clearly differentiated from the two surnames
Nice to have
• They are free to present their best proposals. I will bring them immediate feedback to the extent you can go see their designs. Complete data for card and logo files will give the winner the

```html
<!DOCTYPE html>
<html lang="en">
<head>
<meta charset="utf-8">
<title>ULMIRA — Business Card</title>
<link rel="stylesheet" href="https://fonts.googleapis.com/css2?family=Open+Sans:wght@400;600&display=swap">
<style>
  :root {
    --stage: #000000;
    --card-light: #f3f3f3;
    --ink: #1a1a1a;
    --ink-soft: #2b2b2b;
    --brand-red: #a3101c;
    --red-deep: #8c0d12;
    --red-mid: #b31b24;
    --red-light: #c8313d;
    --white: #ffffff;
  }
  * { margin: 0; padding: 0; box-sizing: border-box; }
  html, body {
    width: 1200px; height: 900px; overflow: hidden;
    background: var(--stage);
    font-family: "Open Sans", Arial, sans-serif;
  }
  .stage { position: relative; width: 1200px; height: 900px; }

  .card { position: absolute; top: 200px; height: 501px; }

  .card--front {
    left: 265px; width: 310px;
    background: var(--card-light);
    border-radius: 62px 0 62px 0;
  }
  .card--back {
    left: 641px; width: 309px;
    border-radius: 0 62px 0 62px;
    background:
      radial-gradient(ellipse 120px 70px at 60% 12%, rgba(120,8,12,.85), transparent 70%),
      radial-gradient(ellipse 150px 60px at 30% 75%, rgba(130,10,14,.8), transparent 70%),
      radial-gradient(ellipse 160px 90px at 25% 45%, rgba(210,70,80,.55), transparent 70%),
      linear-gradient(160deg, var(--red-light) 0%, var(--red-mid) 30%, var(--red-deep) 55%, var(--red-mid) 75%, var(--red-deep) 100%);
  }

  .brand {
    position: absolute; left: 0; right: 0;
    display: flex; flex-direction: column; align-items: center;
  }
  .card--front .brand { top: 44px; }
  .card--back .brand { top: 324px; }

  .brand__mark { width: 34px; height: 34px; margin-bottom: 42px; }
  .card--front .brand__mark { background: var(--brand-red); }
  .card--back .brand__mark { background: var(--white); margin-bottom: 24px; }

  .brand__name {
    font-size: 34px; font-weight: 400; letter-spacing: 12px;
    line-height: 1; padding-left: 12px;
  }
  .card--front .brand__name { color: var(--ink); }
  .card--back .brand__name { color: var(--white); }

  .person { position: absolute; left: 35px; top: 328px; }
  .person__name { font-size: 18px; font-weight: 600; color: var(--brand-red); line-height: 24px; }
  .person__role { font-size: 13.5px; color: var(--ink-soft); line-height: 18px; }

  .contacts { position: absolute; left: 35px; top: 386px; list-style: none; }
  .contacts li {
    display: flex; align-items: center; gap: 7px;
    height: 21px; font-size: 13.5px; color: var(--ink);
  }
  .contacts svg { width: 11px; height: 11px; flex: none; fill: var(--brand-red); }
</style>
</head>
<body>
<main class="stage">

  <section class="card card--front" aria-label="Card front">
    <div class="brand">
      <span class="brand__mark" aria-hidden="true"></span>
      <span class="brand__name">ULMIRA</span>
    </div>

    <div class="person">
      <p class="person__name">Daniel Moreno</p>
      <p class="person__role">Managing Director</p>
    </div>

    <ul class="contacts">
      <li>
        <svg viewBox="0 0 12 12" aria-hidden="true"><path d="M2.3 1 4 1.2 4.8 3.6 3.7 4.6C4.3 6 5.6 7.5 7.3 8.3L8.4 7.2 10.8 8 11 9.7C10.6 10.6 9.8 11 9 11 4.6 10.6 1.4 7.4 1 3 1 2.2 1.4 1.4 2.3 1Z"/></svg>
        (055)-321-7640
      </li>
      <li>
        <svg viewBox="0 0 12 12" aria-hidden="true"><path d="M1 2.5h10v7H1z M1.4 3 6 6.6 10.6 3" stroke="#f3f3f3" stroke-width=".9"/></svg>
        info@ulmira-example.com
      </li>
      <li>
        <svg viewBox="0 0 12 12" aria-hidden="true"><circle cx="6" cy="6" r="5.5"/><path d="M.5 6h11M6 .5c-3 3-3 8 0 11M6 .5c3 3 3 8 0 11" stroke="#f3f3f3" stroke-width=".8" fill="none"/></svg>
        www.ulmira-example.com
      </li>
      <li>
        <svg viewBox="0 0 12 12" aria-hidden="true"><circle cx="6" cy="6" r="5.5"/></svg>
        @ulmiraAT
      </li>
    </ul>
  </section>

  <section class="card card--back" aria-label="Card back">
    <div class="brand">
      <span class="brand__mark" aria-hidden="true"></span>
      <span class="brand__name">ULMIRA</span>
    </div>
  </section>

</main>
</body>
</html>
```